Website Redesign using existing images, copy etc.

I'm looking for a website redesign/refresh of my current WordPress website. I would like to utilize the same photography, a new photo viewer, and an overall refresh of the entire design. This will need to be WordPress with simple accessibility to make changes as we add additional properties and make updates. We auction luxury real estate and luxury yachts for non-distressed sellers. It needs to be simple, luxurious and with ease of use for both web and especially mobile. www.BrindleHarrow.com

```html
<!DOCTYPE html>
<html lang="en">
<head>
<meta charset="utf-8">
<title>Brindle Harrow — Real Estate &amp; Yachts</title>
<link href="https://fonts.googleapis.com/css2?family=Cinzel:wght@400;600;700&family=Roboto:wght@400;500&display=swap" rel="stylesheet">
<style>
:root{
  --gold:#a99675;
  --gold-dark:#8f7d5e;
  --ink:#151515;
  --body:#5b5b5b;
  --cream:#f4f2ee;
  --strip:#ebe8e1;
  --navy:#1d2c56;
  --white:#ffffff;
}
*{box-sizing:border-box;margin:0;padding:0}
html,body{width:1200px;height:4532px;overflow:hidden;background:var(--white)}
body{position:relative;font-family:'Roboto',sans-serif;color:var(--ink)}
.abs{position:absolute}
.mark{display:inline-block;border:2px solid var(--gold);border-radius:50%}
.btn{position:absolute;display:flex;align-items:center;justify-content:space-between;height:40px;padding:0 5px 0 24px;border-radius:20px;font:500 14px 'Roboto',sans-serif;text-decoration:none}
.btn .dot{width:30px;height:30px;border-radius:50%;border:1.5px solid currentColor;margin-left:14px}
.btn-gold{background:var(--gold);color:var(--white)}
.btn-light{background:var(--white);color:var(--gold-dark)}
.btn-outline{background:var(--white);color:var(--gold);border:1.5px solid var(--gold)}
.section-title{position:absolute;left:0;width:1200px;display:flex;justify-content:center;align-items:center;gap:22px;font:700 46px 'Cinzel',serif;color:var(--ink)}
.section-title .mark{width:42px;height:42px}

/* hero */
.hero{top:0;left:0;width:1200px;height:680px;background:linear-gradient(180deg,#1c2a5a 0%,#2a3a6c 45%,#3e3b48 78%,#6a4f37 100%)}
.nav{top:51px;left:111px;width:977px;height:83px;background:rgba(244,244,247,.93);border-radius:6px;display:flex;align-items:center;padding:0 46px}
.brand{display:flex;align-items:center;gap:10px;font:400 17px 'Cinzel',serif;letter-spacing:5px;color:#8d8d8d}
.brand .mark{width:26px;height:26px}
.nav-links{margin-left:auto;display:flex;gap:54px;font:500 14px 'Roboto',sans-serif;color:#3a3a3a}
.hero-title{top:300px;width:1200px;text-align:center;font:700 58px 'Cinzel',serif;color:var(--white)}
.hero-sub{top:386px;width:1200px;text-align:center;font:400 35px 'Cinzel',serif;color:var(--white)}

/* services */
.card{position:absolute;top:911px;width:470px;height:479px;border-radius:28px;overflow:hidden}
.card .label{position:absolute;bottom:50px;width:100%;text-align:center;font:500 25px 'Roboto',sans-serif;letter-spacing:1px;color:var(--white)}

/* about */
.about-img{top:1515px;left:0;width:600px;height:591px;background:linear-gradient(180deg,#c98f76 0%,#d8c6aa 30%,#4f6a3a 60%,#7a5558 100%)}
.about-panel{top:1515px;left:600px;width:600px;height:591px;background:var(--cream)}
.about-title{position:absolute;left:68px;top:114px;display:flex;align-items:center;gap:22px;font:700 44px 'Cinzel',serif}
.about-title .mark{width:42px;height:42px}
.about-kicker{position:absolute;left:68px;top:192px;font:600 17px 'Cinzel',serif;color:var(--gold)}
.about-sub{position:absolute;left:68px;top:230px;font:700 15px 'Cinzel',serif}
.about-copy{position:absolute;left:68px;top:260px;width:430px;font:400 13px/27px 'Roboto',sans-serif;color:var(--body)}

/* sold */
.sold-copy{top:2306px;left:140px;width:920px;text-align:center;font:400 13.5px/27px 'Roboto',sans-serif;color:var(--body)}
.sold-copy p+p{margin-top:26px}
.sold-img{top:2682px;left:111px;width:977px;height:479px;border-radius:22px;background:linear-gradient(180deg,#9fb4c6 0%,#5e6f4c 20%,#2c4f6e 45%,#1c3a5a 100%)}

/* featured */
.feat-title{top:3380px;left:111px;display:flex;align-items:center;gap:22px;font:700 44px 'Cinzel',serif}
.feat-title .mark{width:42px;height:42px}
.feat-copy{top:3452px;left:111px;width:420px;font:400 13px/27px 'Roboto',sans-serif;color:var(--body)}
.feat-img{top:3296px;left:600px;width:488px;height:585px;border-radius:26px;background:linear-gradient(180deg,#b9d3ea 0%,#e6dccb 35%,#7b8a63 55%,#5fbcd0 72%,#d9d3c6 100%)}
.press{top:3692px;left:111px;width:563px;height:101px;background:var(--strip);border-radius:4px;display:flex;align-items:center;justify-content:space-around;padding:0 24px}
.press span{display:block;background:#b9b3a6;border-radius:3px}

/* teaser cards */
.teaser{position:absolute;top:3974px;width:458px;height:241px;border-radius:14px;background:linear-gradient(180deg,#2c1d1a 0%,#4a2d22 60%,#231615 100%)}
.teaser h3{position:absolute;top:78px;width:100%;display:flex;justify-content:center;align-items:center;gap:12px;font:700 29px 'Cinzel',serif;color:var(--white)}
.teaser h3 .mark{width:28px;height:28px}

/* footer */
.foot-brand{top:4315px;width:1200px;display:flex;justify-content:center;align-items:center;gap:16px;font:400 25px 'Cinzel',serif;letter-spacing:8px;color:#8d8d8d}
.foot-brand .mark{width:38px;height:38px}
.foot-ring{top:4300px;left:498px;width:204px;height:204px;border:1.5px solid #efece6;border-radius:50%}
.foot-nav{top:4387px;left:0;width:1200px;display:flex;justify-content:center;gap:82px;font:500 14px 'Roboto',sans-serif;color:var(--ink)}
.social{top:4435px;left:569px;display:flex;gap:12px}
.social span{width:27px;height:27px;border-radius:50%;background:var(--gold);display:block}
.copyright{top:4482px;width:1200px;text-align:center;font:400 11px 'Roboto',sans-serif;color:#666}
</style>
</head>
<body>

<section class="hero abs" role="img" aria-label="Luxury yacht moored at dusk beside a historic waterfront city with a bell tower">
</section>
<nav class="nav abs">
  <div class="brand">BRINDLE <span class="mark"></span> HARROW</div>
  <div class="nav-links"><span>Home</span><span>About Us</span><span>Our Services</span><span>Portfolio</span><span>Contact Us</span></div>
</nav>
<h1 class="hero-title abs">Welcome To Brindle Harrow</h1>
<p class="hero-sub abs">Real Estate &amp; Yachts</p>
<a class="btn btn-gold" style="top:466px;left:334px;width:268px">Browse Upcoming Auctions<span class="dot"></span></a>
<a class="btn btn-light" style="top:466px;left:627px;width:238px">Browse Past Successes<span class="dot"></span></a>

<h2 class="section-title" style="top:796px"><span class="mark"></span>OUR SERVICES</h2>
<div class="card" style="left:111px;background:linear-gradient(180deg,#c9b79a 0%,#b98a2c 30%,#9ea4a8 60%,#101622 100%)" role="img" aria-label="Luxury yachts docked at a marina among autumn trees">
  <span class="label">LUXURY YACHTS</span>
</div>
<div class="card" style="left:619px;background:linear-gradient(180deg,#1e3fa0 0%,#c9c6c0 35%,#6a6460 65%,#0e1320 100%)" role="img" aria-label="Modern white luxury villa lit at twilight">
  <span class="label">LUXURY REAL ESTATE</span>
</div>

<div class="about-img abs" role="img" aria-label="Mediterranean estate with palm trees and a brick driveway at sunset"></div>
<section class="about-panel abs">
  <h2 class="about-title"><span class="mark"></span>ABOUT US</h2>
  <p class="about-kicker">Over One Billion Dollars of Auctions Marketed</p>
  <p class="about-sub">Real Estate &amp; Yachts</p>
  <p class="about-copy">The experience of hearing the auctioneer's final proclamation of "SOLD!" is unparalleled. Whether it's the initial meeting with the seller at their estate or yacht, or the triumphant raising of the paddle by the winning buyer, we relish every moment of the process and the ensuing festivities. We're confident that you will, too.</p>
  <a class="btn btn-gold" style="top:413px;left:68px;width:156px">Read More<span class="dot"></span></a>
</section>

<h2 class="section-title" style="top:2226px"><span class="mark"></span>SOLD BY BRINDLE HARROW</h2>
<div class="sold-copy abs">
  <p>Brindle Harrow is a top-tier destination for luxury property auctions, having overseen the auction marketing of numerous high-end estates and yachts. Our team of luxury home auction experts is committed to helping property owners obtain the best value for their assets while ensuring a timely sale. Whether you have an expansive compound or a metropolitan penthouse, Brindle Harrow has the necessary skills and expertise to facilitate various luxury real estate auctions.</p>
  <p>What's even better? Our team takes care of every aspect of the process in cooperation with tour realtor/broker, including property tours, photography and cinematography, marketing advertising, public relations and more. Apart from high-end real estate auctions, we can also organize and execute luxury yacht auctions to help boat owners find qualified buyers for their vessels.</p>
</div>
<a class="btn btn-gold" style="top:2562px;left:441px;width:148px">Read More<span class="dot"></span></a>
<a class="btn btn-outline" style="top:2562px;left:605px;width:154px">Get Started<span class="dot"></span></a>
<div class="sold-img abs" role="img" aria-label="Aerial view of a waterfront estate on a wooded peninsula at dusk"></div>

<div class="feat-img abs" role="img" aria-label="Mediterranean mansion with arched loggias behind an infinity pool"></div>
<h2 class="feat-title abs"><span class="mark"></span>AS FEATURED IN</h2>
<p class="feat-copy abs">By offering top-tier properties and vessels globally, along with strategic auction dates, exceptional marketing tactics, and a diligent public relations team, even the most prominent media outlets have taken notice. Check out some of our latest press features.</p>
<a class="btn btn-gold" style="top:3593px;left:111px;width:156px">View Press<span class="dot"></span></a>
<div class="press abs" aria-label="Press outlets">
  <span style="width:64px;height:34px"></span>
  <span style="width:78px;height:24px"></span>
  <span style="width:82px;height:14px"></span>
  <span style="width:60px;height:30px"></span>
  <span style="width:36px;height:36px"></span>
</div>

<div class="teaser" style="left:114px" role="img" aria-label="Grand estate facade lit at night">
  <h3><span class="mark"></span>ABOUT US</h3>
  <a class="btn btn-gold" style="top:140px;left:152px;width:156px">Learn More<span class="dot"></span></a>
</div>
<div class="teaser" style="left:628px" role="img" aria-label="Grand estate facade lit at night">
  <h3><span class="mark"></span>UPCOMING EVENTS</h3>
  <a class="btn btn-gold" style="top:140px;left:138px;width:156px">Browse Here<span class="dot"></span></a>
</div>

<footer>
  <div class="foot-ring abs"></div>
  <div class="foot-brand abs">BRINDLE <span class="mark"></span> HARROW</div>
  <div class="foot-nav abs"><span>Home</span><span>About Us</span><span>Our Services</span><span>Portfolio</span><span>Contact Us</span></div>
  <div class="social abs"><span></span><span></span></div>
  <p class="copyright abs">© Copyright 2023 | All Rights Reserved.</p>
</footer>

</body>
</html>
```